Letterhead and email signature block for school

We are a Remote School in the North West of Western Australia and I want to take our logo and use that to create a professional letter head and email signature block. A sample signature block is attached. For the Letterhead; The logo is also attached. I like the Orange and black combination of the logo, needs to include motto plus the following contact details;
PMB 4 BROOME WA
Phone: (08) 9170 3158
Fax: (08) 9170 3206
ABN: 41 287 519 302

The email signature block needs to have the following;
Dale Owen Wrenfield
Principal
Tern Ridge Hill RCS
Phone: (08) 9170 3158
Fax: (08) 9170 3206
Mobile: 0488 613 947
Email: Dale.Wrenfield@schoolnet-kx.org.au

Target Market(s)

Parents

Industry/Entity Type

Education

Contact Information for Business Card

Dale Owen Wrenfield
Principal
Tern Ridge Hill RCS
Phone: (08) 9170 3158
Fax: (08) 9170 3206
Mobile: 0488 613 947

Colors
f37122
000000

Requirements
Must have
• see breif

```html
<!DOCTYPE html>
<html lang="en">
<head>
<meta charset="utf-8">
<title>Tern Ridge Hill RCS — Letterhead</title>
<link href="https://fonts.googleapis.com/css2?family=Roboto+Condensed:wght@400;700&family=Open+Sans:wght@400&display=swap" rel="stylesheet">
<style>
  :root {
    --orange: #f37122;
    --black: #000000;
    --ink: #1e1e1e;
    --muted: #6d6d6d;
    --paper: #fffdfa;
    --backdrop: #f5dfc2;
    --swoosh-grey: #ececec;
    --swoosh-peach: #fbe6d6;
  }
  * { margin: 0; padding: 0; box-sizing: border-box; }
  html, body {
    width: 1200px; height: 784px; overflow: hidden;
    background: var(--backdrop);
  }
  .letterhead {
    position: absolute;
    left: 337px; top: 20px;
    width: 526px; height: 744px;
    background: var(--paper);
    overflow: hidden;
    box-shadow: 0 6px 18px rgba(120, 80, 40, 0.18);
  }
  .edge-band {
    position: absolute; left: 0; top: 0; bottom: 0;
    width: 9px;
    background: linear-gradient(180deg, var(--orange) 0 78%, #3a3a3a 78%, var(--black) 90%, #a0a0a0 100%);
  }
  .swooshes {
    position: absolute; left: 0; top: 0;
    width: 526px; height: 744px;
  }
  .watermark {
    position: absolute;
    left: 90px; top: 200px;
    width: 220px; height: 230px;
    border-radius: 50%;
    background: radial-gradient(ellipse at center, rgba(243,113,34,0.10), rgba(190,190,190,0.07) 60%, rgba(255,255,255,0) 75%);
  }
  .brand {
    position: absolute;
    right: 30px; top: 28px;
    display: flex; flex-direction: column; align-items: flex-end; gap: 3px;
  }
  .brand-row { display: flex; align-items: center; gap: 7px; }
  .brand-dot {
    width: 14px; height: 14px; border-radius: 50%;
    background: var(--orange);
  }
  .brand-name {
    font-family: "Roboto Condensed", sans-serif;
    font-weight: 700; font-size: 15px; color: var(--ink);
  }
  .brand-motto {
    font-family: "Open Sans", sans-serif;
    font-size: 6.5px; color: var(--muted);
  }
  .contact {
    position: absolute;
    right: 30px; bottom: 40px;
    font-style: normal;
  }
  .contact-name {
    font-family: "Roboto Condensed", sans-serif;
    font-weight: 400; font-size: 15px; color: var(--ink);
    margin-bottom: 3px;
  }
  .contact-list { list-style: none; }
  .contact-item {
    display: flex; align-items: center; gap: 6px;
    font-family: "Open Sans", sans-serif;
    font-size: 9px; color: var(--muted);
    line-height: 14px;
  }
  .contact-bullet {
    width: 7px; height: 7px; border-radius: 50%;
    background: var(--orange);
    flex: none;
  }
</style>
</head>
<body>
  <main class="letterhead">
    <svg class="swooshes" viewBox="0 0 526 744" aria-hidden="true">
      <path d="M9 180 C 60 330, 150 520, 330 744 L9 744 Z" fill="#fff4ec"/>
      <path d="M40 120 C 70 300, 160 520, 300 744" fill="none" stroke="var(--swoosh-grey)" stroke-width="14"/>
      <path d="M20 160 C 60 340, 150 540, 270 744" fill="none" stroke="var(--swoosh-peach)" stroke-width="10"/>
      <path d="M70 110 C 110 280, 200 470, 360 700" fill="none" stroke="#f3f3f3" stroke-width="7"/>
    </svg>
    <div class="watermark" role="img" aria-label="Faint enlarged school emblem watermark"></div>

    <header class="brand">
      <div class="brand-row">
        <span class="brand-dot"></span>
        <span class="brand-name">Tern Ridge Hill RCS</span>
      </div>
      <span class="brand-motto">Learning Together, Growing Strong</span>
    </header>

    <address class="contact">
      <div class="contact-name">Tern Ridge Hill RCS</div>
      <ul class="contact-list">
        <li class="contact-item"><span class="contact-bullet"></span>PMB 4 BROOME WA</li>
        <li class="contact-item"><span class="contact-bullet"></span>(08) 9170 3158</li>
        <li class="contact-item"><span class="contact-bullet"></span>(08) 9170 3206</li>
        <li class="contact-item"><span class="contact-bullet"></span>ABN: 41 287 519 302</li>
      </ul>
    </address>

    <div class="edge-band"></div>
  </main>
</body>
</html>
```